VELKO Website Redesign in Wix

Task:
Create a new design for all pages of the VELKO technology website in Wix. Specifications are:
Color palette preferences: black, white, gray, purple, blue. See VELKO Ref Doc provided.
Please refer to the VELKO_ref doc for a sample of the desired color palette
Typesetting must be in Montserrat
Brand will be that of a Marketing Technology company
Looking for vibrant, highly engaging images and organized, digestible flow. Open to suggestions
Required format is Wix.
VELKO logo does NOT need to be redesigned. Please use the files provided for the VELKO logo.
Look and feel
Each slider illustrates characteristics of the customer's brand and the style your logo design should communicate.

```html
<!DOCTYPE html>
<html lang="en">
<head>
<meta charset="utf-8">
<title>VELKO Website Redesign</title>
<link href="https://fonts.googleapis.com/css2?family=Montserrat:wght@400;500;600;700&display=swap" rel="stylesheet">
<style>
:root{
  --board:#5b5c60;
  --white:#ffffff;
  --ink:#1b1b22;
  --muted:#4a4a55;
  --line:#d9d9de;
  --black:#000000;
  --violet:#3c1878;
  --indigo:#2b2ab4;
  --indigo-text:#2d2aa8;
  --plum-text:#41207e;
  --logo-1:#f6efe7;
  --logo-2:#e3e0e4;
  --logo-3:#dde7f3;
  --logo-4:#f3ecda;
  --logo-5:#efeff1;
}
*{margin:0;padding:0;box-sizing:border-box}
html,body{width:1200px;height:2361px;overflow:hidden;background:var(--board);font-family:'Montserrat',sans-serif;color:var(--ink)}
.board{position:absolute;left:0;top:0;width:1309px;height:2576px;transform:scale(0.91673);transform-origin:0 0}

.page{position:absolute;top:51px;width:593px;height:2474px;background:var(--white);overflow:hidden}
.page--violet{left:45px;--heading:var(--indigo-text);--number:rgba(120,116,212,.62);--cta:var(--violet);--band:var(--indigo);--submit:var(--violet);--we:#4b45c6;--hero-a:#24094f;--hero-b:#5d1c9c}
.page--indigo{left:671px;--heading:var(--plum-text);--number:rgba(140,122,182,.62);--cta:var(--indigo);--band:#3d1679;--submit:var(--indigo);--we:#6b3fa2;--hero-a:#3a3aa8;--hero-b:#6468d6}

.abs{position:absolute}
.center{left:0;width:100%;text-align:center}

/* hero */
.hero{left:0;top:0;width:593px;height:283px;background:radial-gradient(ellipse at 60% 40%,var(--hero-b),var(--hero-a) 75%)}
.brand{font-weight:500;letter-spacing:4px;font-size:14px;color:var(--white)}
.hero .brand{left:56px;top:15px}
.nav{right:56px;top:18px;display:flex;gap:22px;font-size:8px;color:var(--white)}
.hero-title{top:81px;font-size:70px;line-height:1;font-weight:600;letter-spacing:18px;color:var(--white);padding-left:18px}
.hero-title sup{font-size:9px;letter-spacing:0;vertical-align:top;position:relative;top:2px}
.hero-tagline{top:157px;font-size:7.5px;line-height:13px;color:var(--white)}
.pill{display:inline-block;width:70px;height:22px;line-height:22px;border-radius:11px;font-size:7px;font-weight:600;text-align:center}
.hero-cta{left:261px;top:192px;background:var(--white);color:var(--violet)}

/* section headings */
.kicker{font-size:9px;font-weight:500;letter-spacing:3px;color:var(--ink)}
.heading{font-size:26px;font-weight:600;letter-spacing:7px;color:var(--heading)}

/* services */
.rule{left:288px;width:1px;background:var(--line)}
.number{font-size:74px;font-weight:700;line-height:1;color:var(--number);letter-spacing:2px;z-index:2}
.card{width:111px;height:127px;background:var(--white);box-shadow:0 2px 8px rgba(0,0,0,.12);z-index:1}
.card .glyph{position:absolute;left:28px;top:36px;width:56px;height:56px;border-radius:6px;background:linear-gradient(135deg,#ececf1,#d7d7de)}
.svc-title{font-size:10px;font-weight:600;letter-spacing:3px;color:var(--ink);white-space:nowrap}
.svc-text{font-size:7.6px;line-height:13.6px;color:var(--muted);width:140px}
.more-cta{left:261px;top:1176px;background:var(--cta);color:var(--white)}

/* about */
.about-photo{left:55px;top:1331px;width:483px;height:206px}
.page--violet .about-photo{background:linear-gradient(120deg,#3a3f4a,#7b7470 45%,#c7bfb4)}
.page--indigo .about-photo{background:linear-gradient(120deg,#d8cfc6,#a9958a 45%,#cfd4dd)}
.we-are{left:88px;font-size:68px;font-weight:600;letter-spacing:6px;line-height:1;color:var(--we)}
.about-card{left:294px;top:1489px;width:204px;height:221px;background:var(--white);box-shadow:0 2px 8px rgba(0,0,0,.15);padding:19px 23px;font-size:7px;line-height:12.7px;color:var(--muted)}
.about-card p+p{margin-top:12.7px}

/* partners */
.partners{left:0;top:1861px;width:593px;height:203px;display:flex}
.partner{flex:1;display:flex;flex-direction:column;align-items:center;justify-content:center;gap:6px;font-size:12px;font-weight:500;color:#2a2a30}
.partner span{font-size:9px;font-weight:500}
.partner:nth-child(1){background:var(--logo-1)}
.partner:nth-child(2){background:var(--logo-2)}
.partner:nth-child(3){background:var(--logo-3)}
.partner:nth-child(4){background:var(--logo-4)}
.partner:nth-child(5){background:var(--logo-5)}

/* contact */
.contact{left:0;top:2064px;width:593px;height:308px;background:var(--band);color:var(--white)}
.contact .kicker{color:var(--white);top:54px}
.contact .heading{color:var(--white);top:70px}
.contact .sub{top:106px;font-size:8px}
.field{height:21px;background:var(--white);color:var(--ink);font-size:7.5px;line-height:21px;padding-left:12px}
.submit{left:110px;top:235px;width:371px;height:21px;background:var(--submit);color:var(--white);font-size:8px;line-height:21px;text-align:center}

/* footer */
.footer{left:0;top:2372px;width:593px;height:54px;background:var(--black);color:var(--white)}
.socials{left:54px;top:23px;display:flex;gap:21px}
.socials i{width:8px;height:8px;border-radius:50%;background:var(--white);display:block}
.footer-contact{right:60px;top:22px;font-size:7px}
.base .brand{color:var(--ink);left:56px;top:2443px}
.copyright{right:56px;top:2446px;font-size:7.5px;letter-spacing:1px;color:var(--muted)}
</style>
</head>
<body>
<div class="board">

  <section class="page page--violet">
    <div class="abs hero" role="img" aria-label="Deep purple abstract network of connected points">
      <div class="abs brand">VELKO</div>
      <nav class="abs nav"><span>Services</span><span>About</span><span>Contact</span></nav>
      <h1 class="abs center hero-title">VELKO<sup>TM</sup></h1>
      <p class="abs center hero-tagline">Increase and perfect your connection with consumers using<br>VELKO™'s patented self-service content delivery technology.</p>
      <a class="abs pill hero-cta">Learn More</a>
    </div>

    <p class="abs center kicker" style="top:328px">OUR</p>
    <h2 class="abs center heading" style="top:342px">SERVICES</h2>

    <div class="abs rule" style="top:384px;height:81px"></div>
    <div class="abs card" style="left:139px;top:495px"><div class="glyph" role="img" aria-label="Gear with rising bar chart icon"></div></div>
    <div class="abs number" style="left:112px;top:455px">01</div>
    <h3 class="abs svc-title" style="left:304px;top:496px">CORPORATE SUBSCRIBTIONS</h3>
    <p class="abs svc-text" style="left:304px;top:520px">Neque porro quisquam est, qui dolorem ipsum quia dolor sit amet, consectetur, adipisci velit, sed quia non numquam eius modi tempa incidunt ut labore et dolore magnam aliquam.</p>

    <div class="abs rule" style="top:647px;height:81px"></div>
    <h3 class="abs svc-title" style="left:104px;top:752px">AD TECH LICENSING</h3>
    <p class="abs svc-text" style="left:104px;top:776px">Neque porro quisquam est, qui dolorem ipsum quia dolor sit amet, consectetur, adipisci velit, sed quia non numquam eius modi tempa incidunt ut labore et dolore magnam aliquam.</p>
    <div class="abs card" style="left:337px;top:751px"><div class="glyph" role="img" aria-label="Certificate document with seal icon"></div></div>
    <div class="abs number" style="left:397px;top:714px">02</div>

    <div class="abs rule" style="top:892px;height:81px"></div>
    <div class="abs card" style="left:139px;top:1002px"><div class="glyph" role="img" aria-label="Laptop with gear and circuit lines icon"></div></div>
    <div class="abs number" style="left:105px;top:965px">03</div>
    <h3 class="abs svc-title" style="left:305px;top:1004px">PLATFORM INTEGRATIONS</h3>
    <p class="abs svc-text" style="left:304px;top:1028px">Neque porro quisquam est, qui dolorem ipsum quia dolor sit amet, consectetur, adipisci velit, sed quia non numquam eius modi tempa incidunt ut labore et dolore magnam aliquam.</p>

    <a class="abs pill more-cta">View More</a>

    <h2 class="abs center heading" style="top:1271px">ABOUT</h2>
    <div class="abs about-photo" role="img" aria-label="Business team reviewing charts around a desk with laptops"></div>
    <div class="abs we-are" style="top:1483px;opacity:.85">WE</div>
    <div class="abs we-are" style="top:1539px">ARE</div>
    <div class="abs about-card">
      <p>Whether you're marketing software, selling a product, or looking to close a deal – find out your target market and quickly modify your campaigns to reach consumers silently and securely.</p>
      <p>Our platform goes far beyond basic ad optimization to deliver individualized content that immediately increases engagement over any communication medium with embedded tones.Quis autem vel eum iure reprehenderit qui in ea voluptate velit esse quam nihil molestiae consequatur.</p>
    </div>

    <p class="abs center kicker" style="top:1787px">PROVEN SUCCESS IN</p>
    <h2 class="abs center heading" style="top:1801px">INNOVATION</h2>
    <div class="abs partners">
      <div class="partner">Nexora<span>1998</span></div>
      <div class="partner">Signal Harbor<span>2001</span></div>
      <div class="partner">Stride<span>2003</span></div>
      <div class="partner">Clearsight<span>2003</span></div>
      <div class="partner">VELKO<span>2005</span></div>
    </div>

    <div class="abs contact">
      <p class="abs center kicker">BE IN</p>
      <h2 class="abs center heading">TOUCH</h2>
      <p class="abs center sub">What Can We Help You With?</p>
      <div class="abs field" style="left:110px;top:146px;width:181px">Name</div>
      <div class="abs field" style="left:300px;top:146px;width:181px">Email</div>
      <div class="abs field" style="left:110px;top:175px;width:371px">Subject</div>
      <div class="abs field" style="left:110px;top:205px;width:371px">Type Your Message Here....</div>
      <div class="abs submit">Submit</div>
    </div>

    <footer class="abs footer">
      <div class="abs socials"><i></i><i></i><i></i><i></i></div>
      <p class="abs footer-contact">Email Us: info@velkotech.com &nbsp;|&nbsp; Tel: 1-866-TRY-VELKO</p>
    </footer>
    <div class="base">
      <div class="abs brand">VELKO</div>
      <p class="abs copyright">Copyrights@2022.All Rights Reserved</p>
    </div>
  </section>

  <section class="page page--indigo">
    <div class="abs hero" role="img" aria-label="Team working together in an office under a blue colour wash">
      <div class="abs brand">VELKO</div>
      <nav class="abs nav"><span>Services</span><span>About</span><span>Contact</span></nav>
      <h1 class="abs center hero-title" style="top:88px;font-size:64px">VELKO<sup>TM</sup></h1>
      <p class="abs center hero-tagline" style="top:159px">Increase and perfect your connection with consumers using<br>VELKO™'s patented self-service content delivery technology.</p>
      <a class="abs pill hero-cta" style="top:189px">Learn More</a>
    </div>

    <p class="abs center kicker" style="top:328px">OUR</p>
    <h2 class="abs center heading" style="top:342px">SERVICES</h2>

    <div class="abs rule" style="top:384px;height:81px"></div>
    <div class="abs card" style="left:139px;top:495px"><div class="glyph" role="img" aria-label="Gear with rising bar chart icon"></div></div>
    <div class="abs number" style="left:112px;top:455px">01</div>
    <h3 class="abs svc-title" style="left:304px;top:496px">CORPORATE SUBSCRIBTIONS</h3>
    <p class="abs svc-text" style="left:304px;top:520px">Neque porro quisquam est, qui dolorem ipsum quia dolor sit amet, consectetur, adipisci velit, sed quia non numquam eius modi tempa incidunt ut labore et dolore magnam aliquam.</p>

    <div class="abs rule" style="top:647px;height:81px"></div>
    <h3 class="abs svc-title" style="left:104px;top:752px">AD TECH LICENSING</h3>
    <p class="abs svc-text" style="left:104px;top:776px">Neque porro quisquam est, qui dolorem ipsum quia dolor sit amet, consectetur, adipisci velit, sed quia non numquam eius modi tempa incidunt ut labore et dolore magnam aliquam.</p>
    <div class="abs card" style="left:337px;top:751px"><div class="glyph" role="img" aria-label="Certificate document with seal icon"></div></div>
    <div class="abs number" style="left:397px;top:714px">02</div>

    <div class="abs rule" style="top:892px;height:81px"></div>
    <div class="abs card" style="left:139px;top:1002px"><div class="glyph" role="img" aria-label="Laptop with gear and circuit lines icon"></div></div>
    <div class="abs number" style="left:105px;top:965px">03</div>
    <h3 class="abs svc-title" style="left:305px;top:1004px">PLATFORM INTEGRATIONS</h3>
    <p class="abs svc-text" style="left:304px;top:1028px">Neque porro quisquam est, qui dolorem ipsum quia dolor sit amet, consectetur, adipisci velit, sed quia non numquam eius modi tempa incidunt ut labore et dolore magnam aliquam.</p>

    <a class="abs pill more-cta">View More</a>

    <h2 class="abs center heading" style="top:1271px">ABOUT</h2>
    <div class="abs about-photo" role="img" aria-label="Smiling colleagues gathered around a laptop"></div>
    <div class="abs we-are" style="top:1483px;opacity:.85">WE</div>
    <div class="abs we-are" style="top:1539px">ARE</div>
    <div class="abs about-card">
      <p>Whether you're marketing software, selling a product, or looking to close a deal – find out your target market and quickly modify your campaigns to reach consumers silently and securely.</p>
      <p>Our platform goes far beyond basic ad optimization to deliver individualized content that immediately increases engagement over any communication medium with embedded tones.Quis autem vel eum iure reprehenderit qui in ea voluptate velit esse quam nihil molestiae consequatur.</p>
    </div>

    <p class="abs center kicker" style="top:1787px">PROVEN SUCCESS IN</p>
    <h2 class="abs center heading" style="top:1801px">INNOVATION</h2>
    <div class="abs partners">
      <div class="partner">Nexora<span>1998</span></div>
      <div class="partner">Signal Harbor<span>2001</span></div>
      <div class="partner">Stride<span>2003</span></div>
      <div class="partner">Clearsight<span>2003</span></div>
      <div class="partner">VELKO<span>2005</span></div>
    </div>

    <div class="abs contact">
      <p class="abs center kicker">BE IN</p>
      <h2 class="abs center heading">TOUCH</h2>
      <p class="abs center sub">What Can We Help You With?</p>
      <div class="abs field" style="left:110px;top:146px;width:181px">Name</div>
      <div class="abs field" style="left:300px;top:146px;width:181px">Email</div>
      <div class="abs field" style="left:110px;top:175px;width:371px">Subject</div>
      <div class="abs field" style="left:110px;top:205px;width:371px">Type Your Message Here....</div>
      <div class="abs submit">Submit</div>
    </div>

    <footer class="abs footer">
      <div class="abs socials"><i></i><i></i><i></i><i></i></div>
      <p class="abs footer-contact">Email Us: info@velkotech.com &nbsp;|&nbsp; Tel: 1-866-TRY-VELKO</p>
    </footer>
    <div class="base">
      <div class="abs brand">VELKO</div>
      <p class="abs copyright">Copyrights@2022.All Rights Reserved</p>
    </div>
  </section>

</div>
</body>
</html>
```